Tide & Thistle Website Creation For Online Spirits Sales via MerrowVats.com

Want a Website developed that I will use to partner with Merrow Vats to sell my signature rum online. Merrow Vats will add the final code to make the website an e-commerce site. Website should have links to Social media pages, recipies, About, news and events, products. I have he domain name already just need a designer to make the website look professional. Need website capable of being viewed on iPhone and Android devices. Please use the color scheme that is on the label. The brand motto is: Celebrate Life With Family old and new friends. The bottle sent in the images will be replaced with and actual high resolution image of the bottle when it is produce on 27 DEC 21. Can give the selected designer access to develop the website. I have the hostbramble.com domain name. Final code will be added by a designer from MerrowVats.com to make it a e-commerce store.
Updates

I added more information to refine the design I wanted. I should have had this information available to the designers when I started the project.

Target Market(s)

Target Market is 25-50 year old who drink rum

Industry/Entity Type

Spirits. Using Website to sell Rum online

Number of Pages Required

1 page

Font styles to use
Sans Serif

Colors
00AB8E
00BBA5
67D7C9
C6EFE9
E9F9F6

Requirements
Must have
• Must look elegant and of high class. Rum is being market as a premium unnamed rum.
Nice to have
• Video of people drinking, smiling and celebrating

```html
<!DOCTYPE html>
<html lang="en">
<head>
<meta charset="UTF-8">
<title>Tide &amp; Thistle</title>
<link href="https://fonts.googleapis.com/css2?family=Oswald:wght@400;500;600&family=Lato:wght@400;700&display=swap" rel="stylesheet">
<style>
:root{
  --teal:#00AB8E;
  --teal-2:#00BBA5;
  --teal-3:#67D7C9;
  --mint:#C6EFE9;
  --mint-soft:#E9F9F6;
  --ink:#222;
  --grey:#555;
  --paper:#efefed;
  --footer:#1d1d1d;
  --white:#fff;
}
*{box-sizing:border-box;margin:0;padding:0}
html,body{width:1200px;height:2924px;overflow:hidden}
body{font-family:'Lato',sans-serif;color:var(--ink);background:var(--white);position:relative}
.head{font-family:'Oswald',sans-serif;text-transform:uppercase}
.btn{display:inline-block;background:var(--teal);color:var(--white);font-family:'Oswald',sans-serif;font-size:17px;letter-spacing:1px;padding:16px 34px;text-transform:uppercase}

/* nav */
.nav{position:absolute;top:0;left:0;width:1200px;height:140px;background:var(--white);display:flex;align-items:center;padding:0 60px}
.nav-links{display:flex;gap:30px;font-family:'Oswald',sans-serif;font-size:16px;text-transform:uppercase;letter-spacing:.5px}
.nav-links .active{color:var(--teal)}
.nav-left{width:440px}
.brand{flex:1;display:flex;flex-direction:column;align-items:center;gap:6px}
.brand-dot{width:46px;height:46px;border-radius:50%;background:var(--ink)}
.brand-name{font-family:'Oswald',sans-serif;font-weight:500;font-size:26px;color:var(--ink);letter-spacing:1px}
.nav-right{width:440px;display:flex;justify-content:flex-end;align-items:center;gap:30px}

/* hero */
.hero{position:absolute;top:140px;left:0;width:1200px;height:690px;background:linear-gradient(180deg,#3f6f9a 0%,#7ea7c2 30%,#5d7a3c 55%,#2f4a1c 100%)}
.hero-copy{position:absolute;top:120px;width:100%;text-align:center;color:var(--white)}
.hero-title{font-size:56px;font-weight:500;line-height:1.15;letter-spacing:1px}
.hero-sub{font-size:22px;margin:16px auto 34px;width:560px;line-height:1.4}
.dots{display:flex;gap:12px;justify-content:center}
.dots span{width:10px;height:10px;border-radius:50%;background:rgba(255,255,255,.55)}
.dots span.on{background:var(--white)}
.hero .dots{position:absolute;bottom:54px;width:100%}

/* about */
.about{position:absolute;top:830px;left:0;width:1200px;height:590px;background:var(--paper)}
.about-bottles{position:absolute;left:160px;top:70px;width:250px;height:460px;background:linear-gradient(180deg,#d9a35a,#b5702a);border-radius:30px 30px 10px 10px}
.about-copy{position:absolute;left:522px;top:120px;width:560px}
.about-title{font-size:46px;font-weight:400;letter-spacing:1px}
.about-lead{color:var(--teal);font-weight:700;font-size:22px;line-height:1.35;margin:14px 0 14px}
.about-copy p{font-size:16px;line-height:1.5;color:var(--grey);margin-bottom:10px}
.about-copy .btn{margin-top:22px}

/* recipes */
.recipes{position:absolute;top:1420px;left:0;width:1200px;height:540px;background:var(--mint-soft)}
.section-title{font-size:46px;font-weight:400;text-align:center;padding-top:36px;letter-spacing:1px}
.recipe-list{display:flex;gap:34px;padding:30px 72px 0}
.recipe{width:330px;text-align:center}
.recipe-photo{height:200px;background:linear-gradient(160deg,#c7a46a,#6f7d4a)}
.recipe:nth-child(2) .recipe-photo{background:linear-gradient(160deg,#e0a04e,#5a4a2f)}
.recipe:nth-child(3) .recipe-photo{background:linear-gradient(160deg,#a8b98a,#6a5a44)}
.recipe-name{color:var(--teal);font-size:22px;font-weight:500;margin:16px 0 8px;letter-spacing:1px}
.recipe p{font-size:15px;line-height:1.45;color:var(--grey);padding:0 24px}

/* testimonials */
.testimonials{position:absolute;top:1960px;left:0;width:1200px;height:540px;background:var(--white)}
.video{position:absolute;left:72px;top:56px;width:460px;height:420px;background:linear-gradient(150deg,#8a9a4c,#4e5a2c 60%,#2f3a1a)}
.video svg{position:absolute;left:188px;top:168px}
.testi-copy{position:absolute;left:612px;top:128px;width:500px}
.testi-title{font-size:46px;font-weight:400;letter-spacing:1px}
.testi-quote{font-size:21px;line-height:1.5;margin:22px 0 12px}
.testi-name{color:var(--teal);font-size:17px}
.testi-copy .dots{justify-content:flex-start;margin-top:60px}
.testi-copy .dots span{background:#bbb}
.testi-copy .dots span.on{background:var(--teal)}

/* footer */
.footer{position:absolute;top:2500px;left:0;width:1200px;height:424px;background:var(--footer);color:var(--white)}
.foot-top{position:absolute;top:58px;left:72px;right:72px;height:110px;display:flex;align-items:center}
.foot-brand{display:flex;flex-direction:column;align-items:center;gap:6px;width:240px}
.foot-brand .brand-dot{background:var(--white)}
.foot-brand .brand-name{color:var(--white)}
.foot-divider{width:2px;height:110px;background:#666;margin:0 32px}
.foot-sub{font-family:'Oswald',sans-serif;font-size:22px;letter-spacing:1px;margin-right:30px}
.foot-input{width:395px;height:56px;background:var(--white);color:var(--ink);font-family:'Oswald',sans-serif;font-size:15px;display:flex;align-items:center;padding-left:18px}
.foot-btn{height:56px;width:120px;background:var(--teal);font-family:'Oswald',sans-serif;font-size:16px;display:flex;align-items:center;justify-content:center}
.foot-links{position:absolute;top:256px;width:100%;display:flex;justify-content:center;gap:38px;font-family:'Oswald',sans-serif;font-size:16px}
.copyright{position:absolute;top:298px;width:100%;text-align:center;font-size:14px;color:#bbb}
.social{position:absolute;top:332px;width:100%;display:flex;justify-content:center;gap:18px}
.social span{width:18px;height:18px;border-radius:50%;background:var(--white)}
</style>
</head>
<body>

<header class="nav">
  <nav class="nav-left nav-links">
    <span class="active">Home</span><span>About</span><span>Products</span><span>Recipes</span>
  </nav>
  <div class="brand">
    <span class="brand-dot"></span>
    <span class="brand-name">TIDE &amp; THISTLE</span>
  </div>
  <div class="nav-right">
    <nav class="nav-links"><span>News &amp; Events</span><span>Contact</span></nav>
    <svg width="22" height="22" viewBox="0 0 22 22" aria-label="Account"><circle cx="11" cy="7" r="5" fill="#00AB8E"/><path d="M2 21c0-5 4-8 9-8s9 3 9 8z" fill="#00AB8E"/></svg>
  </div>
</header>

<section class="hero" role="img" aria-label="Sugar cane field under a blue sky with a path running through it">
  <div class="hero-copy">
    <h1 class="head hero-title">Set up your E-Commerce<br>with Tide &amp; Thistle</h1>
    <p class="hero-sub">The No 1 solution for direct to consumer E-Commerce services within the Beverage industry.</p>
    <span class="btn">Read more</span>
  </div>
  <div class="dots"><span class="on"></span><span></span><span></span><span></span></div>
</section>

<section class="about">
  <div class="about-bottles" role="img" aria-label="Three bottles of Tide &amp; Thistle rum"></div>
  <div class="about-copy">
    <h2 class="head about-title">About Tide &amp; Thistle</h2>
    <p class="about-lead">The pioneer of the white-label approach within the Direct To Consumer channel.</p>
    <p>Tide &amp; Thistle offers custom e-commerce solutions for emerging and established brands looking to use technology as a tool for reaching new customers.</p>
    <p>Tide &amp; Thistle fulfillment services operate through a national network of licensed retailers, shipping carriers, and customer service professionals to guarantee the best fulfillment and logistics practices.</p>
    <span class="btn">Read more</span>
  </div>
</section>

<section class="recipes">
  <h2 class="head section-title">Our Recipes</h2>
  <div class="recipe-list">
    <article class="recipe">
      <div class="recipe-photo" role="img" aria-label="Friends sharing drinks at an outdoor table"></div>
      <h3 class="head recipe-name">Doloremque</h3>
      <p>Nemo enim ipsam voluptatem quia voluptas sit aspernatur aut odit aut fugit, sed quia consequ.</p>
    </article>
    <article class="recipe">
      <div class="recipe-photo" role="img" aria-label="Glasses raised in a toast at sunset"></div>
      <h3 class="head recipe-name">Doloremque</h3>
      <p>Nemo enim ipsam voluptatem quia voluptas sit aspernatur aut odit aut fugit, sed quia consequ.</p>
    </article>
    <article class="recipe">
      <div class="recipe-photo" role="img" aria-label="Guest enjoying a drink outdoors"></div>
      <h3 class="head recipe-name">Doloremque</h3>
      <p>Nemo enim ipsam voluptatem quia voluptas sit aspernatur aut odit aut fugit, sed quia consequ.</p>
    </article>
  </div>
</section>

<section class="testimonials">
  <div class="video" role="img" aria-label="Video of friends celebrating together with drinks">
    <svg width="84" height="84" viewBox="0 0 84 84"><circle cx="42" cy="42" r="38" fill="none" stroke="#fff" stroke-width="5"/><path d="M33 26l26 16-26 16z" fill="#fff"/></svg>
  </div>
  <div class="testi-copy">
    <h2 class="head testi-title">Testimonials</h2>
    <p class="testi-quote">“We would probably not be where we are today had it not been for Tide &amp; Thistle partnership”.</p>
    <p class="testi-name">Dorian K.</p>
    <div class="dots"><span class="on"></span><span></span><span></span><span></span></div>
  </div>
</section>

<footer class="footer">
  <div class="foot-top">
    <div class="foot-brand"><span class="brand-dot"></span><span class="brand-name">TIDE &amp; THISTLE</span></div>
    <span class="foot-divider"></span>
    <span class="foot-sub">SUBSCRIBE EMAIL</span>
    <span class="foot-input">EMAIL ADDRESS</span>
    <span class="foot-btn">SUBSCRIBE</span>
  </div>
  <nav class="foot-links"><span>HOME</span><span>ABOUT</span><span>PRODUCTS</span><span>RECIPES</span><span>NEWS &amp; EVENTS</span><span>CONTACT</span></nav>
  <p class="copyright">© Copyright 2021 . CompanyName All rights reserved</p>
  <div class="social" aria-label="Social media links"><span></span><span></span><span></span><span></span><span></span></div>
</footer>

</body>
</html>
```